QVR business card

Need a business card for a company that provides instructional design and elearning development services. The website is here: http://quorvane.studio/

I'm attaching a current logo, as well as the old business card design. While I like to keep it clean, the old design is too simplistic for my liking. The only idea I want to reuse from the old design is placing industry jargon on the back of the card, just need a better way to present it. But if you have other ideas for the back--feel free to experiment.

Please use the colors complementary to the color we have on the website. Thank you!

```html
<!DOCTYPE html>
<html lang="en">
<head>
<meta charset="utf-8">
<title>QVR business card</title>
<link rel="stylesheet" href="https://fonts.googleapis.com/css2?family=Open+Sans:wght@400;700&family=Open+Sans+Condensed:wght@700&family=PT+Sans+Narrow:wght@400&display=swap">
<style>
  :root {
    --teal: #21b4ad;
    --teal-dark: #1a9f99;
    --sand: #dcd29f;
    --ink: #2f2f2f;
    --rule: #9a9a9a;
    --paper: #ffffff;
    --stage: #e6e6e6;
  }
  * { box-sizing: border-box; margin: 0; padding: 0; }
  html, body { width: 1200px; height: 873px; overflow: hidden; }
  body {
    background: var(--stage);
    position: relative;
    font-family: "Open Sans", Arial, sans-serif;
  }
  .card {
    position: absolute;
    top: 282px;
    width: 540px;
    height: 308px;
    box-shadow: 0 3px 10px rgba(0,0,0,0.18);
    overflow: hidden;
  }

  /* Back side */
  .card-back { left: 45px; background: var(--teal); color: var(--paper); }
  .back-question {
    position: absolute;
    left: 24px; top: 22px;
    font-family: "Open Sans Condensed", "Arial Narrow", sans-serif;
    font-weight: 700;
    font-size: 62px;
    line-height: 64px;
    letter-spacing: 1px;
  }
  .back-divider {
    position: absolute;
    left: 200px; top: 22px;
    width: 2px; height: 262px;
    background: var(--paper);
  }
  .jargon-list {
    position: absolute;
    left: 218px; top: 18px;
    list-style: none;
    font-family: "PT Sans Narrow", "Arial Narrow", sans-serif;
    font-size: 31px;
    line-height: 46px;
    text-transform: uppercase;
    white-space: nowrap;
  }

  /* Front side */
  .card-front { left: 615px; background: var(--paper); color: var(--ink); }
  .brand {
    position: absolute;
    left: 28px; top: 44px;
    display: flex; align-items: center; gap: 10px;
  }
  .brand-mark { width: 26px; height: 26px; background: var(--teal); }
  .brand-name {
    font-weight: 700;
    font-size: 34px;
    color: var(--sand);
    letter-spacing: 1px;
  }
  .holder {
    position: absolute;
    right: 30px; top: 154px;
    text-align: right;
  }
  .holder-name {
    font-weight: 700;
    font-size: 15px;
    color: var(--teal);
    text-transform: uppercase;
  }
  .holder-title { font-size: 13px; margin-top: 6px; }
  .holder-rule {
    position: absolute;
    left: 26px; top: 176px;
    width: 410px; height: 1px;
    background: var(--rule);
  }
  .contacts {
    position: absolute;
    left: 26px; top: 220px;
    list-style: none;
    font-size: 13px;
    line-height: 18px;
  }
  .contacts li { display: flex; align-items: center; gap: 7px; }
  .contacts svg { width: 11px; height: 11px; fill: var(--teal); }
  .front-band { position: absolute; left: 0; bottom: 0; width: 540px; height: 14px; }
</style>
</head>
<body>

<section class="card card-back" aria-label="Card back">
  <h1 class="back-question">HOW<br>CAN<br>WE<br>HELP?</h1>
  <div class="back-divider"></div>
  <ul class="jargon-list">
    <li>Mobile Learning SCORM</li>
    <li>Instructional Design LMS</li>
    <li>MOOCs eLearning HTML5</li>
    <li>Adult Learning Theory</li>
    <li>Gamification Classroom</li>
    <li>xAPI Blended Learning</li>
  </ul>
</section>

<section class="card card-front" aria-label="Card front">
  <div class="brand">
    <span class="brand-mark"></span>
    <span class="brand-name">QVR</span>
  </div>

  <div class="holder-rule"></div>
  <div class="holder">
    <p class="holder-name">Marcus Teller</p>
    <p class="holder-title">Managing Director</p>
  </div>

  <ul class="contacts">
    <li>
      <svg viewBox="0 0 12 12" aria-hidden="true"><path d="M2 1h3l1 3-1.5 1a7 7 0 0 0 2.5 2.5L8 6l3 1v3a1 1 0 0 1-1 1A9 9 0 0 1 1 2a1 1 0 0 1 1-1z"/></svg>
      555-014-2273
    </li>
    <li>
      <svg viewBox="0 0 12 12" aria-hidden="true"><path d="M1 3h10v7H1z M1 3l5 4 5-4" fill="none" stroke="#21b4ad" stroke-width="1.4"/></svg>
      mteller@quorvane.studio
    </li>
    <li>
      <svg viewBox="0 0 12 12" aria-hidden="true"><circle cx="6" cy="6" r="5" fill="none" stroke="#21b4ad" stroke-width="1.3"/><path d="M1 6h10M6 1c-3 3-3 7 0 10M6 1c3 3 3 7 0 10" fill="none" stroke="#21b4ad" stroke-width="1"/></svg>
      www.quorvane.studio
    </li>
  </ul>

  <svg class="front-band" viewBox="0 0 540 14" preserveAspectRatio="none" aria-hidden="true">
    <polygon points="0,0 262,0 276,14 0,14" fill="var(--teal)"/>
    <polygon points="268,0 540,0 540,14 282,14" fill="var(--sand)"/>
  </svg>
</section>

</body>
</html>
```